Computer consultant business card

Bexil Software is a newly started computer consulting company. It's a small one-man company that provides mostly Vornix applications but also websites in collaboration with designers. I'm running this company on the side of full time university studies.

I want the final design to be clean and memorable. Be creative! :)

Some inspiration:
http://www.pixelmarta.com/design/48317
http://www.pixelmarta.com/design/2739164/business-card-design-by-frostlynk
http://www.pixelmarta.com/design/604281/business-card-design-by-koralind-vestrabanu

See attachment for my company logo.
Updates

I would like to thank everyone for submitting! I'll need a couple of days to review and ultimately select a design.

Target Market(s)

Non-technical entrepreneurs and small companies.

Industry/Entity Type

University

Requirements
Must have
• My company logo.
In any way, both colors from my logo.
First- and last name, e-mail and phone number.
Double-sided design.
Nice to have
• Something creative with the symbol in my logo

```html
<!DOCTYPE html>
<html lang="en">
<head>
<meta charset="utf-8">
<title>Bexil Software — Business Card</title>
<link rel="stylesheet" href="https://fonts.googleapis.com/css2?family=Mulish:wght@400;600;700&family=Open+Sans:wght@400&display=swap">
<style>
  :root {
    --ink: #333234;
    --brand-blue: #4470b8;
    --white: #ffffff;
    --backdrop: #e6e1d9;
    --card-black: #050505;
    --slate-top: #2e2f35;
    --slate-bottom: #4b5b85;
    --label: #1e1a16;
  }
  * { box-sizing: border-box; margin: 0; padding: 0; }
  html, body { width: 1200px; height: 788px; overflow: hidden; }
  body {
    position: relative;
    background: var(--backdrop);
    font-family: "Mulish", "Century Gothic", sans-serif;
  }
  .side-label {
    position: absolute;
    width: 200px;
    text-align: center;
    font-family: "Open Sans", sans-serif;
    font-size: 20px;
    color: var(--label);
  }
  .card {
    position: absolute;
    width: 525px;
    height: 298px;
    border-radius: 20px;
    overflow: hidden;
    box-shadow: 0 3px 10px rgba(0,0,0,0.25);
  }
  .card--front, .card--back-light { background: var(--white); }
  .card--back-black { background: var(--card-black); }
  .card--back-slate {
    background: radial-gradient(ellipse at 60% 95%, var(--slate-bottom) 0%, #3d4661 45%, var(--slate-top) 100%);
  }
  .brand {
    position: absolute;
    left: 0; right: 0;
    display: flex;
    align-items: center;
    justify-content: center;
    gap: 20px;
  }
  .brand__dot {
    border-radius: 50%;
    background: var(--brand-blue);
    flex: none;
  }
  .brand__name {
    font-weight: 700;
    letter-spacing: 1px;
    line-height: 1;
  }
  .brand--dark .brand__name { color: var(--ink); }
  .brand--light .brand__name { color: var(--white); }
  .holder {
    position: absolute;
    top: 188px;
    left: 0; right: 0;
    text-align: center;
    color: var(--ink);
  }
  .holder__name { font-size: 17px; font-weight: 700; }
  .holder__role { font-size: 12.5px; font-weight: 400; margin-left: 2px; }
  .contact-bar { position: absolute; left: 0; bottom: 0; width: 525px; height: 32px; }
  .contact-bar__text {
    position: absolute;
    bottom: 8px;
    font-size: 13px;
    color: var(--white);
    letter-spacing: 0.3px;
  }
  .contact-bar__phone { left: 62px; }
  .contact-bar__email { left: 330px; }
  .web-address {
    position: absolute;
    left: 0; right: 0;
    text-align: center;
    font-size: 17px;
    letter-spacing: 4px;
  }
  .web-address--dark { color: var(--ink); }
  .web-address--light { color: var(--white); }
  .texture {
    position: absolute;
    border-radius: 50%;
  }
</style>
</head>
<body>

  <div class="side-label" style="left:220px; top:34px;">Front</div>
  <div class="side-label" style="left:796px; top:34px;">Back - 1</div>
  <div class="side-label" style="left:224px; top:404px;">Back - 2</div>
  <div class="side-label" style="left:796px; top:404px;">Back - 3</div>

  <!-- Front -->
  <section class="card card--front" style="left:57px; top:75px;">
    <div class="brand brand--dark" style="top:70px;">
      <span class="brand__dot" style="width:62px; height:62px;"></span>
      <span class="brand__name" style="font-size:56px;">Bexil</span>
    </div>
    <p class="holder">
      <span class="holder__name">First Name Last Name -</span>
      <span class="holder__role">Designation</span>
    </p>
    <svg class="contact-bar" viewBox="0 0 525 32" aria-hidden="true">
      <polygon points="0,0 230,0 250,32 0,32" fill="var(--ink)"/>
      <polygon points="241,0 525,0 525,32 261,32" fill="var(--brand-blue)"/>
    </svg>
    <span class="contact-bar__text contact-bar__phone">+12 345 6789</span>
    <span class="contact-bar__text contact-bar__email">info@website.com</span>
  </section>

  <!-- Back 1 -->
  <section class="card card--back-light" style="left:622px; top:75px;">
    <div class="brand brand--dark" style="top:96px;">
      <span class="brand__dot" style="width:74px; height:74px;"></span>
      <span class="brand__name" style="font-size:68px;">Bexil</span>
    </div>
    <p class="web-address web-address--dark" style="top:249px;">www.website.com</p>
  </section>

  <!-- Back 2 -->
  <section class="card card--back-black" style="left:54px; top:446px;">
    <div class="texture" role="img" aria-label="Perforated metal texture, upper left"
         style="left:20px; top:-90px; width:300px; height:200px; background:radial-gradient(ellipse, rgba(120,120,125,0.45) 0%, rgba(0,0,0,0) 70%);"></div>
    <div class="texture" role="img" aria-label="Perforated metal texture, lower right"
         style="left:320px; top:170px; width:260px; height:200px; background:radial-gradient(ellipse, rgba(130,125,130,0.45) 0%, rgba(0,0,0,0) 70%);"></div>
    <div class="brand brand--light" style="top:108px;">
      <span class="brand__dot" style="width:80px; height:80px;"></span>
      <span class="brand__name" style="font-size:72px;">Bexil</span>
    </div>
    <p class="web-address web-address--light" style="top:254px;">www.website.com</p>
  </section>

  <!-- Back 3 -->
  <section class="card card--back-slate" style="left:622px; top:446px;">
    <div class="brand brand--light" style="top:108px;">
      <span class="brand__dot" style="width:80px; height:80px;"></span>
      <span class="brand__name" style="font-size:72px;">Bexil</span>
    </div>
    <p class="web-address web-address--light" style="top:254px;">www.website.com</p>
  </section>

</body>
</html>
```